Harborview Estates Business Card for Apartment Buildings

Create business cards for resident managers who run apartment buildings. The audience is the public who are searching for apartment rentals, and current residents who live at the apartment building. Key design element will be incorporating the company logo, however, the logo cannot dominate. The building name and manager name are more important than the logo. Current business card design leaves little room for copy, so we may need to reduce the size on the current card to allow for more space for copy.

Target Market(s)

Adults 18-65 years of age, who are looking for an apartment rental, plus current residents who live at our apartment buildings.

Industry/Entity Type

Property Management

Contact Information for Business Card

A major design element will be use of the company logo. Important property and manager contact information must be part of the design. The size of the logo will need to be reduced to make room for building and manager contact copy.

Font styles to use
Sans Serif

Colors
3176b5
000000
959595
ffffff

Requirements
Must have
• 1) Incorporate the company logo.
• 2) Use the company colors (dark blue, black/grey, over white).
• 3) FEATURE THE BUILDING NAME
• 4) FEATURE THE MANAGER NAME
• 5) The company name is less important than BUILDING and MANAGER
• 6) Manager contact information
• **SEE ATTACHED CREATIVE BRIEF**
Nice to have
• 1) Back of card logo watermark
• 2) Ability to write notes on back of carfd
Should not have
• Avoid letting the company logo dominate the card, the building name and manager are more important than the company logo.

```html
<!DOCTYPE html>
<html lang="en">
<head>
<meta charset="utf-8">
<title>Harborview Estates Business Card</title>
<link href="https://fonts.googleapis.com/css2?family=Roboto:wght@400;500;700&family=Roboto+Condensed:wght@500&display=swap" rel="stylesheet">
<style>
  :root {
    --brand-blue: #1a6aa8;
    --band-blue: #1768a6;
    --text-grey: #454545;
    --paper: #f4f4f4;
    --stage: #e6e6e6;
    --watermark: #e2e4e7;
    --white: #ffffff;
  }
  * { margin: 0; padding: 0; box-sizing: border-box; }
  html, body { width: 1200px; height: 960px; overflow: hidden; }
  body {
    background: var(--stage);
    font-family: "Roboto", Arial, sans-serif;
    position: relative;
  }
  .card {
    position: absolute;
    width: 600px;
    height: 343px;
    background: var(--paper);
    box-shadow: 0 2px 6px rgba(0,0,0,0.25);
    overflow: hidden;
  }
  .card-front { left: 314px; top: 113px; }
  .card-back { left: 311px; top: 472px; }

  .name-band { position: absolute; left: 0; top: 45px; }
  .manager-name {
    position: absolute; left: 43px; top: 61px;
    font-family: "Roboto Condensed", Arial, sans-serif;
    font-weight: 500; font-size: 23px; color: var(--white);
    letter-spacing: -0.2px;
  }
  .manager-title {
    position: absolute; left: 43px; top: 88px;
    font-size: 15px; color: var(--white);
  }
  .company-mark {
    position: absolute; right: 39px; top: 74px;
    display: flex; align-items: center; gap: 8px;
  }
  .company-dot {
    width: 14px; height: 14px; border-radius: 50%;
    background: var(--brand-blue);
  }
  .company-name {
    font-weight: 500; font-size: 19px; color: var(--brand-blue);
  }

  .contact-list {
    position: absolute; left: 44px; top: 231px;
    list-style: none;
  }
  .contact-list li {
    display: flex; align-items: center;
    height: 19px; font-size: 14px; color: var(--text-grey);
  }
  .contact-list svg { width: 14px; height: 14px; margin-right: 8px; fill: var(--brand-blue); }

  .property-info {
    position: absolute; right: 39px; top: 224px;
    text-align: right; color: var(--text-grey);
  }
  .building-name {
    font-weight: 500; font-size: 21px; color: var(--brand-blue);
    line-height: 26px;
  }
  .address { font-size: 14px; line-height: 19px; }
  .website { font-size: 14px; margin-top: 9px; }

  .watermark {
    position: absolute; left: 0; right: 0; top: 0; bottom: 0;
    display: flex; align-items: center; justify-content: center; gap: 18px;
  }
  .watermark-dot {
    width: 60px; height: 60px; border-radius: 50%;
    background: var(--watermark);
  }
  .watermark-name {
    font-weight: 500; font-size: 44px; color: var(--watermark);
  }
</style>
</head>
<body>
  <section class="card card-front">
    <svg class="name-band" width="340" height="82" viewBox="0 0 340 82" aria-hidden="true">
      <path d="M0 0 H300 Q312 45 330 82 H0 Z" fill="var(--band-blue)"/>
    </svg>
    <div class="manager-name">Marisol Delgado</div>
    <div class="manager-title">Resident Manager</div>

    <div class="company-mark">
      <span class="company-dot"></span>
      <span class="company-name">Harborview Estates</span>
    </div>

    <ul class="contact-list">
      <li><svg viewBox="0 0 16 16"><path d="M3.5 1 L6 1 L7 5 L5.3 6.3 Q6.8 9.4 9.7 10.7 L11 9 L15 10 L15 12.5 Q14.5 15 12 15 Q1 13.5 1 3.5 Q1.5 1 3.5 1Z"/></svg>555-210-4387</li>
      <li><svg viewBox="0 0 16 16"><path d="M4 0 H12 Q13 0 13 1 V15 Q13 16 12 16 H4 Q3 16 3 15 V1 Q3 0 4 0Z M4.5 2 V12.5 H11.5 V2Z M7 13.5 H9 V14.8 H7Z"/></svg>555-318-6024</li>
      <li><svg viewBox="0 0 16 16"><path d="M4 1 H11 V5 H4Z M1 6 H15 V12 H12 V15 H4 V12 H1Z M5 10 V13.5 H11 V10Z"/></svg>555-462-9150</li>
      <li><svg viewBox="0 0 16 16"><path d="M1 3 H15 V13 H1Z M2 4.3 V5 L8 9 L14 5 V4.3 L8 8Z"/></svg>marisol@harborviewest.com</li>
    </ul>

    <div class="property-info">
      <div class="building-name">Bayside Court Apartments</div>
      <div class="address">2145 Cedar Lane</div>
      <div class="address">Port Lorne, CA 92150</div>
      <div class="website">www.harborviewest.com</div>
    </div>
  </section>

  <section class="card card-back">
    <div class="watermark">
      <span class="watermark-dot"></span>
      <span class="watermark-name">Harborview Estates</span>
    </div>
  </section>
</body>
</html>
```